New and upgraded www.valdmorefunds.com content & design financial markets

We need an upgrade of our site. The current site is www.valdmorefunds.com
Navigation with full site map i.e. the user can select any page from any menu item.

The “Insights” (Insikter) page will remain as is except new design AND with far more possibilities to add thumbnails, picts, videos etc. The user will have to logon to be able to read the full story.

The “Produkter & Tjänster” (“How to invest” in current web) will contain about the same info as the current “How to invest” pages.

Some pages will contain one or more videos and or speaker supported “live” graphics which we will supply. The media content shall be easy to change.

The site will have two languages from start, English and Swedish. There will be more languages added within 1 year or slightly more.

All texts will be provided by us.

I’m attaching a PDF with suggested content for some of the new pages. However this is just content and absolutely no design. We need new design for the total of the site as well as for the graphics.

Expectation info:
These sites (Both major players in our business) can be used as inspiration:
https://www.tarvenholm.com/eu/en/
https://www.brightwellpartners.com/index.html

Below some opt-OUT and opt-IN graphic rules in connection with the Web supporting our business acumen and brand:

Opt-OUT:
- images similar to educational comic books - it signals an authoritarian approach where the customer is small (insubstantial).
- images that signal trading, cyber, mystery and fast-paced business. We are extremely long-term and invest in real companies
- avoid images containing coins, calculators and banknotes. We're not a savings bank company. or payment service-branch
- avoid images of large data flows, because we should not make facts complex, but simple and comprehensible
- avoid sensing pictures of photo models. We are real people who stand for our efforts. We're not going to hide.
- avoid pictures of suits and tie. They signal rigid-banking. We're smart-investment, flexible, adaptable. Rather curl up your sleeves and show that we’re building something valuable.
- avoid pictures of skyscrapers and cool bank pictures - because they signal the more old valuations of big capital and giant banks - that we are not at all. I know we've had clean facades before. As long as we're not talking about bank skyscrapers, I'm in.

Opt-IN
- pictures of Lukas in moderate amount - he is our symbol person
- films with Lukas and explaining graphical films - explaining and clarifying
- images of pedagogy that give the customer a sense of overview and insights that we give to the customers in our service
- illustrations that explain and deepen our work
- pictures and bars that in 3d illustrate our consistent results and stable delivery
- images that signal that we have a full grasp of data, flows and analyses - without the image becoming a space adventure
- use the logo as a grid, shape and colour.
- no genre portraits, rather pictures of real customers - which gives a sense of why they are customers here
- images that support our core i.e. is science, innovation, unrestricted thinking (“out of the box” – (don’t like that sentence)), smart-solutions, data-driven, client-cantered, flexible and adaptable to client needs and expectation.
- Solid - to be trustworthy in any economic climate
- Long term - consistent work and choices. No trading. Numbers talk
- Data-driven - real tech - combining years of work in finance with straight on tech

Presenting on the webpage:
The story in text and illustration
Show the truth - we have a great history to show and give space
Only numbers and graphs that has a meaning - no artificial numbers etc.
Updates

Target Market(s)

Europe

Coding

Coded - Design and coding required

Number of Pages Required

5+ page

Colors

Designer to choose colors to be used in the design.

Requirements
Must have
• Colours in line with www.valdmorefunds.com

```html
<!DOCTYPE html>
<html lang="en">
<head>
<meta charset="utf-8">
<title>Valdmore Funds – Your Personal Investment Advisor</title>
<link href="https://fonts.googleapis.com/css2?family=Lexend:wght@300;400;500&family=Lato:wght@400;700&display=swap" rel="stylesheet">
<style>
:root{
  --blue:#1d4fb0;
  --blue-mid:#1a45a0;
  --blue-deep:#102f86;
  --navy:#2a4f8e;
  --footer:#0c1b3c;
  --ink:#1a1a1a;
  --text:#555;
  --light:#f2f2f2;
  --white:#fff;
}
*{box-sizing:border-box;margin:0;padding:0}
html,body{width:1200px;height:5217px;overflow:hidden}
body{position:relative;background:var(--white);font-family:Lato,sans-serif;color:var(--ink)}
h1,h2,h3,h4,.display{font-family:Lexend,sans-serif;font-weight:400}
.abs{position:absolute}
.btn{position:absolute;display:flex;align-items:center;justify-content:center;border-radius:24px;font-family:Lato,sans-serif;font-weight:700;font-size:15px;text-decoration:none}
.btn-blue{background:var(--blue);color:var(--white)}
.btn-white{background:var(--white);color:var(--blue)}
.btn-outline{border:2px solid var(--white);color:var(--white)}
.photo{position:absolute}

/* header */
.site-header{position:absolute;left:0;top:0;width:1200px;height:72px;background:var(--white)}
.brand{position:absolute;left:88px;top:22px;display:flex;align-items:center;gap:10px;font-family:Lexend,sans-serif;font-size:25px;color:var(--blue-deep)}
.brand i{display:block;width:18px;height:18px;background:var(--blue-deep)}
.nav{position:absolute;top:26px;left:350px;display:flex;gap:34px;font-size:15px;color:#333}
.nav .active{color:var(--blue);border-bottom:2px solid var(--blue);padding-bottom:2px}
.login{left:990px;top:14px;width:120px;height:46px}

/* hero */
.hero{position:absolute;left:0;top:72px;width:1200px;height:554px;background:linear-gradient(90deg,#6d6a66 0%,#b9b2a8 40%,#e6e2dc 60%,#f1efec 100%)}
.hero-title{position:absolute;left:617px;top:120px;display:flex;align-items:center;gap:14px;font-family:Lexend,sans-serif;font-weight:300;font-size:64px;color:var(--blue)}
.hero-title i{display:block;width:54px;height:54px;background:var(--blue-deep)}
.hero-sub{position:absolute;left:617px;top:220px;font-family:Lexend,sans-serif;font-size:28px;color:#111}
.hero-line{position:absolute;left:617px;top:268px;width:520px;font-family:Lexend,sans-serif;font-weight:300;font-size:24px;line-height:28px;color:var(--blue)}
.arrow{position:absolute;top:246px;width:48px;height:48px;border-radius:50%;background:var(--white);display:flex;align-items:center;justify-content:center}

/* features */
.feature{position:absolute;top:626px;width:400px;height:426px;color:var(--white);text-align:center}
.feature h3{position:absolute;top:166px;width:100%;font-size:24px;font-weight:500}
.feature p{position:absolute;top:210px;left:40px;width:320px;font-size:15px;line-height:30px;opacity:.9}
.feature svg{position:absolute;left:172px;top:80px}
.feature .btn{left:126px;top:302px;width:148px;height:46px}

/* about */
.about-bg{position:absolute;left:800px;top:1052px;width:400px;height:631px;background:var(--blue-deep)}
.section-h{font-size:40px;color:var(--ink)}
.body-p{font-size:14.5px;line-height:29px;color:#444}

/* thinking */
.thinking{position:absolute;left:0;top:1683px;width:1200px;height:532px;background:var(--navy);color:var(--white)}

/* approach */
.card{position:absolute;top:2430px;width:329px;height:312px;background:var(--white);box-shadow:0 4px 18px rgba(0,0,0,.16);text-align:center}
.card h4{margin-top:48px;font-size:21px;font-weight:500;line-height:28px;color:var(--ink)}
.card p{margin:18px auto 0;width:290px;font-size:15px;line-height:27px;color:#777}
.card svg{position:absolute;left:148px;top:266px}

/* lists */
.ticks{list-style:none;font-size:14.5px;color:#333}
.ticks li{position:relative;padding-left:34px;line-height:30px}
.ticks li.tick::before{content:"";position:absolute;left:0;top:9px;width:14px;height:12px;border:2px solid var(--blue);border-radius:50% 0 50% 50%}

/* contact */
.contact{position:absolute;left:0;top:4205px;width:1200px;height:620px;background:var(--light)}
.field{position:absolute;background:var(--white);border:1px solid #e2e2e2;font-size:15px;color:#777;padding:14px 16px}

/* footer */
.site-footer{position:absolute;left:0;top:4825px;width:1200px;height:392px;background:var(--footer);color:var(--white)}
.foot-h{position:absolute;top:72px;font-family:Lexend,sans-serif;font-size:20px;font-weight:500}
.foot-list{position:absolute;top:120px;list-style:none;font-size:14.5px;line-height:27px;color:#d7dbe6}
.social{position:absolute;top:136px;left:88px;display:flex;gap:14px}
.social span{width:34px;height:34px;border-radius:50%;display:block}
</style>
</head>
<body>

<header class="site-header">
  <div class="brand"><i></i>Valdmore Funds</div>
  <nav class="nav">
    <span class="active">Home</span><span>Philosophy</span><span>How To Invest</span><span>What We Do</span><span>Contact</span><span>Insights</span>
  </nav>
  <a class="btn btn-blue login">Login</a>
</header>

<section class="hero">
  <div class="photo" role="img" aria-label="Portrait of a smiling advisor in glasses in front of bookshelves" style="left:0;top:0;width:600px;height:554px;background:linear-gradient(180deg,#8a8a86,#b7afa3)"></div>
  <div class="arrow" style="left:20px"><svg width="14" height="14" viewBox="0 0 14 14"><path d="M9 2 4 7l5 5" fill="none" stroke="#111" stroke-width="2.4"/></svg></div>
  <div class="arrow" style="left:1132px"><svg width="14" height="14" viewBox="0 0 14 14"><path d="m5 2 5 5-5 5" fill="none" stroke="#111" stroke-width="2.4"/></svg></div>
  <div class="hero-title"><i></i>Valdmore Funds</div>
  <h2 class="hero-sub">Your Personal Investment Advisor</h2>
  <p class="hero-line">Valdmore Funds is Your Global Reference for Investment Advice</p>
  <a class="btn btn-blue" style="left:617px;top:376px;width:196px;height:50px;font-size:17px">Get Started</a>
</section>

<section>
  <div class="feature" style="left:0;background:var(--blue)">
    <svg width="56" height="60" viewBox="0 0 56 60" fill="none" stroke="#fff" stroke-width="2"><rect x="8" y="24" width="40" height="32" rx="2"/><path d="M16 24V16a12 12 0 0 1 24 0v8"/><circle cx="28" cy="38" r="4"/><path d="M28 42v6"/></svg>
    <h3>Why Choose Us</h3>
    <p>We secure your interests by continuously keeping your Investment optimal</p>
    <a class="btn btn-white">Learn More</a>
  </div>
  <div class="feature" style="left:400px;background:var(--blue-mid)">
    <svg width="60" height="60" viewBox="0 0 60 60" fill="none" stroke="#fff" stroke-width="2"><circle cx="34" cy="16" r="10"/><path d="M34 11v10M31 13h5M31 19h5"/><path d="M4 42h10l10 6h18l12-10-4-3-10 7H30"/><path d="M14 38l8-4h12"/><path d="M4 36v14"/></svg>
    <h3>Investment Intelligence</h3>
    <p>Tailor-made Solutions to Preserve and Grow Wealth in All Market Conditions.</p>
    <a class="btn btn-white">Learn More</a>
  </div>
  <div class="feature" style="left:800px;background:var(--blue-deep)">
    <svg width="56" height="56" viewBox="0 0 56 56" fill="none" stroke="#fff" stroke-width="2"><circle cx="28" cy="28" r="25"/><circle cx="28" cy="28" r="17"/><circle cx="28" cy="24" r="5"/><path d="M20 38a8 8 0 0 1 16 0"/></svg>
    <h3>Client Focus</h3>
    <p>We are dedicated to offer you exceptional service and unbiased financial advice.</p>
    <a class="btn btn-white">Learn More</a>
  </div>
</section>

<section>
  <div class="about-bg"></div>
  <h2 class="abs section-h" style="left:66px;top:1160px">About Us</h2>
  <div class="abs body-p" style="left:66px;top:1220px;width:478px">
    <p>We are a privately held firm dedicated to clients who have entrusted us with their wealth. We act solely and transparently in the best interest of our clients. We pride ourselves on our discretion and confidentiality.</p>
    <p style="margin-top:10px">You can be assured of a totally Client-centric service, high quality, totally unbiased, investment advice. We are fee only based, i.e. we have no affiliations with any financial institutions – we do not take any commission from any investment product provider – We Work Only for You!</p>
  </div>
  <a class="btn btn-blue" style="left:66px;top:1517px;width:164px;height:48px">Learn More</a>
  <div class="photo" role="img" aria-label="Advisor on the phone working at a laptop in a bright office" style="left:602px;top:1162px;width:508px;height:411px;background:linear-gradient(135deg,#c9b9a0,#8d7f6c 55%,#d8d2c6)"></div>
  <svg class="abs" style="left:600px;top:1480px" width="100" height="95" viewBox="0 0 100 95" fill="none" stroke="#b0b0b0" stroke-width="6"><path d="M0 3h95v92"/><path d="M0 33h65v62"/></svg>
</section>

<section class="thinking">
  <div class="abs" style="left:0;top:62px;width:468px;height:400px;background:#fff;box-shadow:0 18px 30px rgba(0,0,0,.35)"></div>
  <div class="photo" role="img" aria-label="Laptop screen showing a blue market growth infographic" style="left:10px;top:80px;width:446px;height:364px;background:linear-gradient(160deg,#f4f6fa 0%,#d6e6f5 45%,#4a9ad8 100%)"></div>
  <div class="abs" style="left:0;top:462px;width:530px;height:8px;background:#d5d5d5"></div>
  <h2 class="abs" style="left:602px;top:114px;font-size:40px">Thinking Beyond</h2>
  <div class="abs" style="left:602px;top:176px;width:520px;font-size:14.5px;line-height:29px;color:#dfe6f2">
    <p>Everything around us is changing in an accelerating pace, so shouldn't the financial markets change too?</p>
    <p style="margin-top:12px">We asked ourselves – is this really how wealth management and investing should work? Is it really necessary to treat clients as just a number in a box? Is this how services should be delivered? How about flexibility?</p>
  </div>
  <a class="btn btn-outline" style="left:602px;top:360px;width:164px;height:48px">Learn More</a>
</section>

<section>
  <h2 class="abs" style="left:0;width:1200px;top:2312px;text-align:center;font-size:40px">Our Approach</h2>
  <p class="abs" style="left:0;width:1200px;top:2380px;text-align:center;font-size:15px;color:#333">Valdmore Funds is truly different – We deliver Investment Services that sets us apart from our contemporaries</p>
  <div class="card" style="left:88px"><h4>Valdmore Investment<br>Management System<br>VIMS®</h4><p>Built on a combination of macroeconomic and fundamental analysis</p><svg width="34" height="12" viewBox="0 0 34 12"><path d="M0 6h31M26 1l5 5-5 5" fill="none" stroke="#1d4fb0" stroke-width="2"/></svg></div>
  <div class="card" style="left:434px"><h4>VIQS ®<br>Investment Generator</h4><p>Valdmore iQ Software VIQS® is designed to analyse, forcast, generate and monitor an infinite number of personalized investment portfolios in a fully automated process &amp; digital system</p><svg width="34" height="12" viewBox="0 0 34 12"><path d="M0 6h31M26 1l5 5-5 5" fill="none" stroke="#1d4fb0" stroke-width="2"/></svg></div>
  <div class="card" style="left:781px"><h4>Services</h4><p style="margin-top:30px">VIMS® &amp; VIQS® enable Valdmore Funds to deliver customized services &amp; solutions to low cost &amp; risks with predictable returns</p><svg width="34" height="12" viewBox="0 0 34 12"><path d="M0 6h31M26 1l5 5-5 5" fill="none" stroke="#1d4fb0" stroke-width="2"/></svg></div>
  <a class="btn btn-blue" style="left:518px;top:2790px;width:164px;height:48px">Learn More</a>
</section>

<section>
  <div class="photo" role="img" aria-label="Advisor presenting to colleagues in a bright meeting room" style="left:0;top:2940px;width:1200px;height:632px;background:linear-gradient(90deg,#f4f4f2 0%,#e8e6e2 45%,#b5aea4 70%,#8f8a84 100%)"></div>
  <h2 class="abs" style="left:90px;top:3040px;width:520px;font-size:40px;line-height:48px">Valdmore Investment Advisory Philosophy</h2>
  <ul class="abs ticks" style="left:90px;top:3144px;width:520px">
    <li class="tick">Systematic Adaption to Market Climate</li>
    <li class="tick">Attractive Risk Returns with Low Portfolio Turnover</li>
    <li class="tick">Europe and U.S. Investment Area</li>
    <li class="tick">Built to Follow or Outperform the Market During Upturns and Avoid</li>
    <li>Large Declines During Long – Term Market Turndowns</li>
    <li class="tick">Continuously Monitoring, Identifying and Implementing to Maintain</li>
    <li>Optimal Portfolio</li>
    <li class="tick">Long – Term Investment Strategy</li>
  </ul>
  <a class="btn btn-blue" style="left:90px;top:3412px;width:164px;height:48px">Learn More</a>
</section>

<section>
  <div class="abs" style="left:0;top:3572px;width:400px;height:633px;background:linear-gradient(135deg,#1b3f9c,#0f2f86)"></div>
  <div class="photo" role="img" aria-label="Hands holding a tablet showing a blue market chart" style="left:88px;top:3680px;width:510px;height:372px;background:linear-gradient(135deg,#e9e9e9,#3a6fc4 45%,#1a3f8f 70%,#cfcfcf)"></div>
  <svg class="abs" style="left:500px;top:4035px" width="100" height="100" viewBox="0 0 100 100" fill="none" stroke="#b0b0b0" stroke-width="6"><path d="M0 3h97v97"/><path d="M30 33h37v67"/></svg>
  <h2 class="abs" style="left:663px;top:3676px;width:500px;font-size:40px;line-height:44px">Valdmore Funds Investment Strategy</h2>
  <ul class="abs ticks" style="left:663px;top:3772px;width:480px">
    <li class="tick">Excellent Historic Performance</li>
    <li class="tick">Value Invest</li>
    <li>Macro</li>
    <li>Fundamental</li>
    <li class="tick">Active Management</li>
    <li class="tick">Risk Control</li>
    <li class="tick">Low Portfolio Turnover</li>
    <li class="tick">Portfolio Management on clients own account</li>
  </ul>
  <a class="btn btn-blue" style="left:663px;top:4036px;width:164px;height:48px">Learn More</a>
</section>

<section class="contact">
  <h2 class="abs" style="left:0;width:1200px;top:100px;text-align:center;font-size:40px">Make a Change!</h2>
  <p class="abs" style="left:0;width:1200px;top:166px;text-align:center;font-family:Lexend,sans-serif;font-weight:300;font-size:26px;color:#333">Contact Us</p>
  <div class="field" style="left:221px;top:213px;width:371px;height:46px">First Name</div>
  <div class="field" style="left:606px;top:213px;width:372px;height:46px">Last Name</div>
  <div class="field" style="left:221px;top:270px;width:371px;height:46px">Email</div>
  <div class="field" style="left:606px;top:270px;width:372px;height:46px">Phone No</div>
  <div class="field" style="left:221px;top:330px;width:757px;height:102px">Message</div>
  <a class="btn btn-blue" style="left:518px;top:465px;width:164px;height:48px">Submit</a>
</section>

<footer class="site-footer">
  <div class="brand" style="left:88px;top:66px;font-size:34px;color:#fff"><i style="width:26px;height:26px;background:#fff"></i>Valdmore Funds</div>
  <div class="social"><span style="background:#3b5bc4"></span><span style="background:#d6362f"></span><span style="background:#e2523f"></span><span style="background:#35a4e8"></span><span style="background:#2f86c9"></span></div>
  <h4 class="foot-h" style="left:444px">LINKS</h4>
  <ul class="foot-list" style="left:444px"><li>Home</li><li>Investment Intelligence</li><li>Thinking Beyond</li><li>What We Do</li><li>Login</li><li>Disclaimer</li><li>Contact Us</li></ul>
  <h4 class="foot-h" style="left:695px">VALDMORE FUNDS</h4>
  <ul class="foot-list" style="left:695px"><li>14 Rue des Tanneurs</li><li>L-2140 Luxembourg</li><li>Luxembourg</li><li>&nbsp;</li><li>Tel: +352 2640 5518</li></ul>
  <h4 class="foot-h" style="left:945px">VALDMORE FUNDS</h4>
  <ul class="foot-list" style="left:945px"><li>52, Harbour Lane</li><li>SLM 2204 Sliema</li><li>Malta</li><li>&nbsp;</li><li>Tel: +356 2145 8830</li></ul>
  <p class="abs" style="left:0;width:1200px;top:358px;text-align:center;font-size:12px;color:#d7dbe6">© Copyrights 2019. The Company Name. All Rights Reserved</p>
</footer>

</body>
</html>
```